BuildLinkHub.com Full Stationery Design

Business Card will have all info on it. Letterhead will not have name, title or mobile number. Keep general feeling very clean, using colors from the logo as accents.
Name:Dale Marchetti
Title:President
Phone: 1-800-555-0142
Cell: 306-555-0187
email: dale@buildlinkhub.example
website: www.buildlinkhub.example
Address:
PO Box 947
Pinecrest, MB
S0J2T0

Target Market(s)

Construction Business owners

Industry/Entity Type

Business

Contact Information for Business Card

Name:Dale Marchetti
Title:President
Phone: 1-800-555-0142
Cell: 306-555-0187
Address:
PO Box 947
Pinecrest, MB
S0J2T0

Font styles to use
Sans Serif

Requirements
Must have
• Clean look
Should not have
• Images or cartoon type characters or tools

```html
<!DOCTYPE html>
<html lang="en">
<head>
<meta charset="utf-8">
<title>BuildLinkHub.com Letterhead</title>
<link href="https://fonts.googleapis.com/css2?family=Open+Sans:wght@400;600&display=swap" rel="stylesheet">
<style>
  :root {
    --backdrop: #f1d6d0;
    --paper: #ffffff;
    --ink: #4a4f57;
    --ink-soft: #7a7f87;
    --accent-orange: #e8501c;
    --accent-slate: #7c8996;
    --tint-peach: #fbeee7;
  }
  * { margin: 0; padding: 0; box-sizing: border-box; }
  html, body {
    width: 1200px; height: 784px; overflow: hidden;
    background: var(--backdrop);
    font-family: "Open Sans", Arial, sans-serif;
  }
  .letterhead {
    position: absolute; left: 314px; top: 22px;
    width: 572px; height: 740px;
    background: var(--paper);
    box-shadow: 0 2px 8px rgba(120, 60, 50, 0.15);
    overflow: hidden;
  }
  .brand {
    position: absolute; left: 36px; top: 30px;
    display: flex; align-items: center; gap: 8px;
  }
  .brand-mark { width: 14px; height: 14px; background: var(--accent-orange); }
  .brand-name { font-weight: 600; font-size: 15px; color: var(--ink); letter-spacing: 0.1px; }
  .tint-block { position: absolute; background: var(--tint-peach); }
  .tint-block.one { right: 0; top: 24px; width: 120px; height: 60px; opacity: 0.7; }
  .tint-block.two { right: 40px; top: 84px; width: 80px; height: 46px; opacity: 0.45; }
  .contact {
    position: absolute; left: 396px; top: 30px;
    list-style: none;
    font-size: 8.5px; line-height: 14px; color: var(--ink-soft);
    white-space: nowrap;
  }
  .contact li { display: flex; align-items: center; gap: 5px; }
  .contact svg { width: 8px; height: 8px; flex: none; }
  .edge-band { position: absolute; left: 0; bottom: 0; height: 6px; }
  .edge-band.orange { width: 74%; background: var(--accent-orange); }
  .edge-band.slate { left: 76%; right: 0; background: var(--accent-slate); }
</style>
</head>
<body>
  <main class="letterhead">
    <div class="brand">
      <span class="brand-mark"></span>
      <span class="brand-name">BuildLinkHub.com</span>
    </div>

    <div class="tint-block one"></div>
    <div class="tint-block two"></div>

    <ul class="contact">
      <li>
        <svg viewBox="0 0 8 8"><circle cx="4" cy="4" r="4" fill="var(--accent-orange)"/><path d="M4 1.6a1.5 1.5 0 0 0-1.5 1.5C2.5 4.3 4 6.2 4 6.2s1.5-1.9 1.5-3.1A1.5 1.5 0 0 0 4 1.6z" fill="#fff"/></svg>
        PO Box 947, Pinecrest, MB  S0J2T0
      </li>
      <li>
        <svg viewBox="0 0 8 8"><circle cx="4" cy="4" r="4" fill="var(--accent-orange)"/><path d="M2.6 2c.4 1.7 1.6 3 3.4 3.6l.3-.8-.9-.5-.4.4C4.3 4.4 3.7 3.8 3.4 3.1l.4-.4-.5-.9z" fill="#fff"/></svg>
        Phone: 1-800-555-0142
      </li>
      <li>
        <svg viewBox="0 0 8 8"><circle cx="4" cy="4" r="4" fill="var(--accent-orange)"/><rect x="2" y="2.7" width="4" height="2.8" fill="#fff"/><path d="M2 2.7l2 1.5 2-1.5" stroke="var(--accent-orange)" stroke-width="0.4" fill="none"/></svg>
        dale@buildlinkhub.example
      </li>
      <li>
        <svg viewBox="0 0 8 8"><circle cx="4" cy="4" r="4" fill="var(--accent-orange)"/><circle cx="4" cy="4" r="2" fill="none" stroke="#fff" stroke-width="0.6"/><path d="M2 4h4M4 2v4" stroke="#fff" stroke-width="0.5"/></svg>
        www.buildlinkhub.example
      </li>
    </ul>

    <div class="edge-band orange"></div>
    <div class="edge-band slate"></div>
  </main>
</body>
</html>
```